Business Card Design

New business card design

Target Market(s)

Residential & Commercial Property Managers

Industry/Entity Type

Plumbing Services

Contact Information for Business Card

Name - Rowan Keddle, title - Director, Phone Number - 0431 286 517, email - rowan@tbk-plumbing.com.au, Company ABN - 73 215 904 386,

Font styles to use
Sans Serif

Colors
0054AA
0677BA
7BADD7
CADEEF
E8F1F8

```html
<!DOCTYPE html>
<html lang="en">
<head>
<meta charset="utf-8">
<title>TBK Plumbing Services – Business Card</title>
<link rel="stylesheet" href="https://fonts.googleapis.com/css2?family=Poppins:wght@300;400;500;600&display=swap">
<style>
  :root {
    --stage: #212121;
    --card-white: #ffffff;
    --brand-blue: #29a9e1;
    --ink: #1d2731;
    --earth: #7a6c62;
    --text-dark: #1a1a1a;
  }
  * { margin: 0; padding: 0; box-sizing: border-box; }
  html, body {
    width: 1200px; height: 780px; overflow: hidden;
    background: var(--stage);
    font-family: "Poppins", sans-serif;
  }
  .stage {
    width: 1200px; height: 780px;
    display: flex; align-items: center; justify-content: center; gap: 40px;
  }
  .card {
    width: 540px; height: 310px; position: relative; overflow: hidden;
  }
  .card--front { background: var(--card-white); }
  .card--back {
    background: var(--brand-blue);
    display: flex; flex-direction: column; align-items: center; justify-content: center;
  }

  /* brand name block */
  .brand { display: flex; flex-direction: column; }
  .brand__row { display: flex; align-items: center; gap: 8px; }
  .brand__name {
    color: var(--ink); font-weight: 400; line-height: 1; letter-spacing: 2px;
  }
  .brand__dot { border-radius: 50%; background: var(--brand-blue); }
  .brand__tagline {
    color: var(--earth); font-weight: 300; text-transform: lowercase;
  }

  .card--front .brand { position: absolute; left: 40px; top: 40px; }
  .card--front .brand__name { font-size: 64px; }
  .card--front .brand__dot { width: 12px; height: 12px; }
  .card--front .brand__tagline { font-size: 9px; letter-spacing: 7px; margin-top: 6px; }

  .card--back .brand { align-items: center; }
  .card--back .brand__name { font-size: 120px; }
  .card--back .brand__dot { width: 20px; height: 20px; background: var(--card-white); }
  .card--back .brand__tagline { font-size: 13px; letter-spacing: 12px; margin-top: 10px; }

  .divider {
    position: absolute; left: 248px; top: 70px;
    width: 1px; height: 200px; background: var(--brand-blue);
  }
  .abn {
    position: absolute; left: 40px; bottom: 40px;
    font-size: 12px; color: var(--brand-blue); font-weight: 400;
  }

  .contact { position: absolute; left: 272px; top: 78px; }
  .contact__name { font-size: 26px; line-height: 1.1; }
  .contact__first { color: var(--brand-blue); font-weight: 600; }
  .contact__last { color: var(--earth); font-weight: 300; }
  .contact__title { font-size: 12px; font-weight: 500; color: var(--text-dark); margin-top: 2px; }
  .contact__list { list-style: none; margin-top: 16px; }
  .contact__item {
    display: flex; align-items: center; gap: 8px;
    font-size: 12px; color: var(--text-dark); margin-bottom: 6px;
  }
  .contact__icon { width: 13px; height: 13px; flex: none; }
</style>
</head>
<body>
<main class="stage">
  <section class="card card--front" aria-label="Business card front">
    <div class="brand">
      <div class="brand__row">
        <span class="brand__name">tbk</span>
        <span class="brand__dot"></span>
      </div>
      <span class="brand__tagline">plumbing services</span>
    </div>
    <div class="divider"></div>
    <p class="abn">ABN - 73 215 904 386,</p>

    <div class="contact">
      <p class="contact__name"><span class="contact__first">Rowan</span> <span class="contact__last">Keddle</span></p>
      <p class="contact__title">Director</p>
      <ul class="contact__list">
        <li class="contact__item">
          <svg class="contact__icon" viewBox="0 0 16 16" aria-hidden="true">
            <path d="M4 1.5l2.2 3-1.3 1.6a8 8 0 0 0 5 5l1.6-1.3 3 2.2-1.3 2.3C7.5 14.5 1.5 8.5 1.7 2.8z" fill="#29a9e1"/>
          </svg>
          <span>0431 286 517</span>
        </li>
        <li class="contact__item">
          <svg class="contact__icon" viewBox="0 0 16 16" aria-hidden="true">
            <rect x="1" y="3" width="14" height="10" rx="1.5" fill="#29a9e1"/>
            <path d="M1.5 4l6.5 5 6.5-5" fill="none" stroke="#fff" stroke-width="1.3"/>
          </svg>
          <span>rowan@tbk-plumbing.com.au</span>
        </li>
        <li class="contact__item">
          <svg class="contact__icon" viewBox="0 0 16 16" aria-hidden="true">
            <circle cx="8" cy="8" r="7" fill="#29a9e1"/>
            <path d="M1 8h14M8 1c-3 3.5-3 10.5 0 14M8 1c3 3.5 3 10.5 0 14" fill="none" stroke="#fff" stroke-width="1"/>
          </svg>
          <span>www.tbk-plumbing.com.au</span>
        </li>
      </ul>
    </div>
  </section>

  <section class="card card--back" aria-label="Business card back">
    <div class="brand">
      <div class="brand__row">
        <span class="brand__name">tbk</span>
        <span class="brand__dot"></span>
      </div>
      <span class="brand__tagline">plumbing services</span>
    </div>
  </section>
</main>
</body>
</html>
```